Halvorsen Ridge Consulting Needs a Letterhead

Tomi, we need a letterhead/banner for our blog, which is titled "Marigold Crossroads". The letterhead/banner should incorporate the enclosed banner image, logo, and the name of our blog ("Marigold Crossroads").

We would also like an alternative design that includes our picture. Here, we have two options that we would like to see.

In all, we would like to see 3 different designs: one banner without any pics; and two banner with two versions of our pictures.

The file size should be able to be resized for the space given to us at our website (http://halvorsen-ridge-consulting.com).

We also need the letterhead/banner by Friday, June 13. Thanks!!

```html
<!DOCTYPE html>
<html lang="en">
<head>
<meta charset="utf-8">
<title>Marigold Crossroads – Blog Banner</title>
<link rel="stylesheet" href="https://fonts.googleapis.com/css2?family=Bebas+Neue&display=swap">
<style>
  :root {
    --banner-bg: #000000;
    --title-yellow: #f6f08e;
  }
  html, body {
    margin: 0;
    padding: 0;
    width: 1200px;
    height: 250px;
    overflow: hidden;
    background: var(--banner-bg);
  }
  .banner {
    position: relative;
    width: 1200px;
    height: 250px;
    background: var(--banner-bg);
  }
  .blog-title {
    position: absolute;
    left: 24px;
    top: 32px;
    margin: 0;
    font-family: "Bebas Neue", "Oswald", sans-serif;
    font-weight: 400;
    font-size: 150px;
    line-height: 106px;
    color: var(--title-yellow);
    letter-spacing: 1px;
    white-space: nowrap;
  }
  .blog-title span { display: block; }
  .company-mark {
    position: absolute;
    right: 28px;
    top: 88px;
    display: flex;
    align-items: center;
    gap: 16px;
  }
  .company-square {
    width: 52px;
    height: 52px;
    background: var(--title-yellow);
    flex: none;
  }
  .company-name {
    margin: 0;
    font-family: "Bebas Neue", "Oswald", sans-serif;
    font-weight: 400;
    font-size: 38px;
    line-height: 38px;
    letter-spacing: 0.5px;
    color: var(--title-yellow);
    white-space: nowrap;
  }
  .company-name span { display: block; }
</style>
</head>
<body>
  <header class="banner">
    <h1 class="blog-title">
      <span>Marigold</span>
      <span>Crossroads</span>
    </h1>
    <div class="company-mark">
      <div class="company-square"></div>
      <p class="company-name">
        <span>Halvorsen Ridge</span>
        <span>Consulting</span>
      </p>
    </div>
  </header>
</body>
</html>
```